Looking for a modern, Professional business card design

We have a simple business card, but are looking for a more modern, professional look. A sample of the basic card is attached as well as the logo. We would also like to add that we offer:
Struggling with your finances?
- Learn to become debt free
- Discover the power of cash
- Control your money instead of it controlling you
Let us help you achieve a new level of financial freedom!
Also, we would like to have a "SPECIAL OFFER!: FREE 30 minute consultation"
Financial Planning

```html
<!DOCTYPE html>
<html lang="en">
<head>
<meta charset="utf-8">
<title>Steadyway Financial Coaching – Business Card</title>
<link rel="stylesheet" href="https://fonts.googleapis.com/css2?family=PT+Sans:ital,wght@0,400;0,700;1,400;1,700&display=swap">
<style>
  :root {
    --backdrop: #3d3d3d;
    --card-white: #ffffff;
    --green-deep: #3e8d3a;
    --green-mid: #5aa832;
    --green-lime: #a9d23b;
    --text-gray: #555555;
    --text-white: #ffffff;
  }
  * { margin: 0; padding: 0; box-sizing: border-box; }
  html, body {
    width: 1105px;
    height: 1200px;
    overflow: hidden;
    background: var(--backdrop);
    font-family: "PT Sans", Arial, sans-serif;
  }
  .canvas {
    position: relative;
    width: 1105px;
    height: 1200px;
  }
  .card {
    position: absolute;
    left: 193px;
    width: 720px;
    height: 412px;
  }

  /* Front */
  .card-front {
    top: 181px;
    background: var(--card-white);
  }
  .name-band {
    position: absolute;
    left: 0;
    top: 65px;
    width: 380px;
    height: 94px;
    background: linear-gradient(90deg, var(--green-mid) 0%, var(--green-mid) 55%, rgba(169,210,59,0.85) 85%, rgba(169,210,59,0) 100%);
    padding: 17px 0 0 42px;
    color: var(--text-white);
  }
  .holder-name {
    font-size: 26px;
    font-weight: 700;
    letter-spacing: 0.5px;
    line-height: 1.1;
  }
  .holder-title {
    font-size: 19px;
    font-weight: 400;
    margin-top: 4px;
  }
  .brand {
    position: absolute;
    left: 392px;
    top: 62px;
    display: flex;
    align-items: center;
    gap: 14px;
  }
  .brand-dot {
    width: 40px;
    height: 40px;
    border-radius: 50%;
    background: var(--green-mid);
    flex: none;
  }
  .brand-name {
    font-size: 27px;
    font-weight: 700;
    line-height: 1.05;
    color: var(--green-deep);
    text-transform: uppercase;
  }
  .contact {
    position: absolute;
    left: 0;
    right: 0;
    top: 317px;
    color: var(--text-gray);
    font-size: 19px;
    text-align: center;
  }
  .contact-row {
    display: flex;
    justify-content: center;
    align-items: center;
    gap: 18px;
    height: 28px;
  }
  .contact-item {
    display: inline-flex;
    align-items: center;
    gap: 7px;
  }
  .contact-item svg { fill: var(--green-mid); flex: none; }

  /* Back */
  .card-back {
    top: 637px;
    height: 410px;
    background: radial-gradient(ellipse 60% 75% at 50% 32%, var(--green-lime) 0%, #7cbb37 45%, var(--green-deep) 100%);
    color: var(--text-white);
    text-align: center;
  }
  .back-brand {
    position: absolute;
    left: 0;
    right: 0;
    top: 70px;
    display: flex;
    justify-content: center;
    align-items: center;
    gap: 16px;
  }
  .back-brand .brand-dot { background: var(--text-white); width: 52px; height: 52px; }
  .back-brand .brand-name { color: var(--text-white); font-size: 34px; text-align: left; }
  .pitch {
    position: absolute;
    left: 0;
    right: 0;
    top: 237px;
  }
  .pitch-heading {
    font-size: 21px;
    font-weight: 700;
    letter-spacing: 0.3px;
    line-height: 30px;
  }
  .pitch-line {
    font-size: 18px;
    font-style: italic;
    line-height: 26.5px;
  }
  .offer {
    font-size: 26px;
    font-weight: 700;
    font-style: italic;
    margin-top: 10px;
  }
</style>
</head>
<body>
<main class="canvas">

  <section class="card card-front" aria-label="Business card front">
    <div class="name-band">
      <div class="holder-name">DANIEL R. HAYES</div>
      <div class="holder-title">Personal Financial Coach</div>
    </div>

    <div class="brand">
      <span class="brand-dot"></span>
      <div class="brand-name">Steadyway<br>Financial Coaching</div>
    </div>

    <div class="contact">
      <div class="contact-row">
        <span class="contact-item">
          <svg width="14" height="22" viewBox="0 0 14 22" aria-hidden="true"><path d="M2 0h10a2 2 0 0 1 2 2v18a2 2 0 0 1-2 2H2a2 2 0 0 1-2-2V2a2 2 0 0 1 2-2zm0 3v14h10V3z"/></svg>
          (205) 555-0142
        </span>
        <span class="contact-item">
          <svg width="18" height="13" viewBox="0 0 18 13" aria-hidden="true"><path d="M0 0h18v1.5L9 7.5 0 1.5z"/><path d="M0 3.3l9 6 9-6V13H0z"/></svg>
          daniel@steadywaycoaching.com
        </span>
      </div>
      <div class="contact-row">
        <span class="contact-item">
          <svg width="18" height="18" viewBox="0 0 18 18" aria-hidden="true"><circle cx="9" cy="9" r="9"/><path d="M5 4c2 1 1 3 3 3s1 3-1 3-1 3-3 2M12 3c-1 2 1 3 2 3s1 3-1 4-1 4 1 4" stroke="#fff" stroke-width="1.4" fill="none"/></svg>
          www.steadywaycoaching.com
        </span>
      </div>
    </div>
  </section>

  <section class="card card-back" aria-label="Business card back">
    <div class="back-brand">
      <span class="brand-dot"></span>
      <div class="brand-name">Steadyway<br>Financial Coaching</div>
    </div>

    <div class="pitch">
      <div class="pitch-heading">STRUGGLING WITH YOUR FINANCES?</div>
      <div class="pitch-line">Learn to become debt free &bull; Discover the power of cash</div>
      <div class="pitch-line">Control your money instead of it controlling you</div>
      <div class="pitch-line">Let us help you achieve a new level of financial freedom!</div>
      <div class="offer">SPECIAL OFFER!: FREE 30 minute consultation</div>
    </div>
  </section>

</main>
</body>
</html>
```